Fitness Equipment Repair Business Needs a Catchy New Business Card

We have an existing business card, however, it is quite plain and boring. We are expanding primarily in the commercial area (gyms, studios, apartment complexes etc). The business card will serve as eye candy to those managers/owners that can't be met for a face to face.
Originally I was planning for a brochure as well, but all of our information is better summarized on our website. (brightloopservice.ca).
I would like the card to match the colour scheme of the website and utilize the logo. It should have a professional clean feel to it, however, a little colouring outside the lines wouldn't hurt.
The example card is for my service technician (Colin Marsh). If possible I would like to be able to edit the text to use for more than one person.

Industry/Entity Type

Appliance Repair

Contact Information for Business Card

Clean, crisp and professional but needs to be eye catching. Preferably using the black, white and red colour scheme matching the website. Double sided would be nice, but is not necessary.

Colors
ec1f27
ffffff
000000

Requirements
Must have
• Must be able to edit name, phone number and title to use for multiple people. Must show the company website (brightloopservice.ca).

```html
<!DOCTYPE html>
<html lang="en">
<head>
<meta charset="utf-8">
<title>Brightloop Service – Business Card</title>
<link rel="stylesheet" href="https://fonts.googleapis.com/css2?family=Open+Sans:wght@400;600&display=swap">
<style>
  :root {
    --brand-red: #ec1f27;
    --ink: #111111;
    --paper: #ffffff;
    --stage-top: #2a2a2a;
    --stage-bottom: #050505;
  }
  * { margin: 0; padding: 0; box-sizing: border-box; }
  html, body { width: 1200px; height: 900px; overflow: hidden; }
  body {
    position: relative;
    background: linear-gradient(180deg, var(--stage-top) 0%, #151515 55%, var(--stage-bottom) 100%);
    font-family: "Open Sans", Arial, sans-serif;
    color: var(--ink);
  }
  .card {
    position: absolute;
    top: 306px;
    height: 271px;
    background: var(--paper);
    border-radius: 12px;
  }
  .card--front { left: 149px; width: 439px; }
  .card--back { left: 608px; width: 441px; }

  /* Front side */
  .brand-mark {
    position: absolute;
    left: 58px; top: 112px;
    width: 150px;
    display: flex; align-items: center; gap: 8px;
  }
  .brand-mark__square {
    width: 14px; height: 14px; background: var(--brand-red); flex: none;
  }
  .brand-mark__name {
    font-size: 17px; font-weight: 600; line-height: 1.2; color: var(--ink);
  }
  .person { position: absolute; left: 225px; top: 50px; }
  .person__name { font-size: 15px; font-weight: 600; color: var(--brand-red); line-height: 1.2; }
  .person__title { font-size: 12px; line-height: 1.3; }
  .address { position: absolute; left: 225px; top: 115px; font-size: 12px; line-height: 15px; }
  .contacts { position: absolute; left: 225px; top: 158px; list-style: none; font-size: 12px; }
  .contacts li { display: flex; align-items: center; height: 16px; }
  .contacts svg { width: 9px; height: 9px; margin-right: 7px; fill: var(--brand-red); flex: none; }

  /* Back side */
  .wordmark {
    position: absolute;
    left: 90px; top: 58px;
    display: flex; align-items: center; gap: 18px;
  }
  .wordmark__square { width: 22px; height: 22px; background: var(--brand-red); flex: none; }
  .wordmark__name {
    font-size: 38px; font-weight: 400; line-height: 44px; color: var(--ink);
  }
  .tagline {
    position: absolute; left: 0; right: 0; top: 212px;
    text-align: center; font-size: 12.5px; color: var(--brand-red);
  }
</style>
</head>
<body>
  <section class="card card--front" aria-label="Business card front">
    <div class="brand-mark">
      <span class="brand-mark__square"></span>
      <span class="brand-mark__name">Brightloop<br>Service</span>
    </div>
    <div class="person">
      <p class="person__name">Colin Marsh</p>
      <p class="person__title">Managing Director</p>
    </div>
    <p class="address">12345, Address Goes Here<br>Country Name, 123456.</p>
    <ul class="contacts">
      <li><svg viewBox="0 0 10 10"><path d="M2.5 0h5a1 1 0 0 1 1 1v8a1 1 0 0 1-1 1h-5a1 1 0 0 1-1-1V1a1 1 0 0 1 1-1zm.5 1.5v6h4v-6z"/></svg>044-123 456 789</li>
      <li><svg viewBox="0 0 10 10"><path d="M2 0.5l2 2-1 1.2c.6 1.3 1.5 2.2 2.8 2.8L7 5.5l2 2-1.2 1.8C4.5 9.5.5 5.5.7 1.7z"/></svg>044-123 456 789</li>
      <li><svg viewBox="0 0 10 10"><path d="M0 2h10v.8L5 5.8 0 2.8zm0 1.8 5 3 5-3V8H0z"/></svg>info@brightloopservice.ca</li>
      <li><svg viewBox="0 0 10 10"><circle cx="5" cy="5" r="4.8"/></svg>www.brightloopservice.ca</li>
    </ul>
  </section>

  <section class="card card--back" aria-label="Business card back">
    <div class="wordmark">
      <span class="wordmark__square"></span>
      <span class="wordmark__name">Brightloop<br>Service</span>
    </div>
    <p class="tagline">When your machines need a spotter, our techs are one call away!</p>
  </section>
</body>
</html>
```